Website Redesign for Non-Profit Ministry & Church

NOTE: Please do not contact me privately — all private inquiries will be ignored.

Individuals seeking spiritual healing, community connection, ministry support and journal-based encounters.

Description of What’s Needed

We need a clean, fresh, inviting website that encourages engagement and connection. The site should feel warm and accessible, draw people in, and clearly present who we are, what we offer, and how visitors can participate. The layout should be straightforward, with well-structured pages (no overlapping objects, minimal layering complexity) and easy to navigate. Use only Google Fonts. All stock photos must be sourced from royalty-free sites and include proper attribution. We will not include a search feature.

Pages to Create
1. Home Page – impactful hero area, clear call-to-action, visual story of ministry, giving/gathering invitation.
2. About Us – vision, mission, leadership, testimonies, history.
3. Meetings & Events – upcoming gatherings, schedule, how to attend, sign-up or interest form.
4. Encounter: “Lanterns by the River” (book) – dedicated page for the book, overview, purchase link or details, journal prompts, imagery.
5. Healing Rooms / Ministry – explain ministry offerings, invite participation, testimonials or case-studies.
6. Live Stream & Links Page – page listing links for YouTube live stream, other platforms, archive links; simple layout.

Colour & Branding

Use colours that blend with our existing logo (attached). The palette should feel contemporary, welcoming, and aligned with ministry themes of restoration, healing and love. Ensure text, button and link colours maintain good contrast for accessibility.

Existing Content & Reference

Please gather available content from our current website in the attachment here for text, images and structure for reuse.

Imagery Guidelines

– Use original photos from our Facebook page or Google Location listing for building or people images when available.
– If generic images are used, ensure they depict appropriate ministry-related buildings or people (community, warm gathering) — avoid generic unrelated stock imagery.
– All photos must be royalty-free or have proper licensing and attribution.
– No overlapping objects or visual clutter; clean layouts with defined sections.

Additional Notes

– Integration: We currently utilise MailChimp for email communication; the design should include a connection/invite to subscribe (via MailChimp) but no blog page is required at this time.
– Payment/Giving: We accept PayPal and already have a giving portal; include clear donation/give buttons or calls-to-action linking to existing giving systems.
– No search function to be included.
– Layouts should avoid complex layering or overlapping elements—designers should work with distinct content blocks, clear visual hierarchy, and straightforward mobile-friendly structure.

Target Market(s)

Industry/Entity Type

Church/Religious institution

Number of Pages Required

5+ page

Requirements
Should not have
• search bar

```html
<!DOCTYPE html>
<html lang="en">
<head>
<meta charset="utf-8">
<title>Mended Kept Whole — Home</title>
<link rel="stylesheet" href="https://fonts.googleapis.com/css2?family=Noto+Sans:wght@500;600;700&family=Roboto:wght@400;500&family=Figtree:wght@400;500&display=swap">
<style>
:root{
  --teal:#13a898;
  --teal-soft:#bfe9e3;
  --purple:#6a2c95;
  --purple-deep:#55207f;
  --green:#0f6b37;
  --ink:#1d1d1f;
  --muted:#3a3a3a;
  --mint:#f1fbf9;
  --grey-band:#f3f3f6;
  --white:#ffffff;
}
*{margin:0;padding:0;box-sizing:border-box}
html,body{width:1200px;height:3581px;overflow:hidden}
body{position:relative;background:var(--white);font-family:"Roboto",sans-serif;color:var(--ink)}
.abs{position:absolute}
.heading{font-family:"Noto Sans",sans-serif;font-weight:700}
.btn{position:absolute;display:flex;align-items:center;justify-content:center;background:var(--teal);color:var(--white);border-radius:30px;font-family:"Noto Sans",sans-serif;font-weight:700;font-size:16px;text-decoration:none}
.rule{position:absolute;height:4px;width:50px;background:var(--teal);border-radius:2px}
.dot{position:absolute;border-radius:50%;background:var(--teal-soft)}

/* header */
.hero-bg{left:0;top:0;width:1200px;height:800px;background:linear-gradient(180deg,#ffffff 0%,var(--mint) 40%,#e9f8f5 100%)}
.brand{left:111px;top:14px;display:flex;align-items:center;gap:10px}
.brand-mark{width:52px;height:52px;border-radius:50%;border:4px solid var(--teal)}
.brand-name{font-family:"Noto Sans",sans-serif;font-weight:700;font-size:22px;line-height:22px;color:var(--green)}
.topbar{left:403px;top:0;width:797px;height:45px;background:var(--teal);border-bottom-left-radius:28px;display:flex;align-items:center;padding-left:120px;gap:48px;color:var(--white);font-size:15.5px;font-weight:500}
.topbar span{display:flex;align-items:center;gap:14px}
.topbar i{width:28px;height:28px;border-radius:50%;background:var(--white);display:flex;align-items:center;justify-content:center}
.nav{left:420px;top:60px;display:flex;gap:20px;font-size:15.5px;color:var(--ink)}
.nav a{color:inherit;text-decoration:none}
.nav .active{color:var(--teal);font-weight:500}

.hero-title{left:104px;top:196px;font-size:78px;line-height:76px}
.hero-title .g{color:var(--green)}.hero-title .p{color:var(--purple)}.hero-title .t{color:var(--teal)}
.hero-text{left:109px;top:360px;width:440px;font-family:"Figtree",sans-serif;font-size:15.5px;line-height:27.5px;color:var(--ink)}
.hero-photo-ring{left:640px;top:168px;width:464px;height:464px;border-radius:50%;background:var(--teal-soft)}
.hero-photo{left:654px;top:182px;width:436px;height:436px;border-radius:50%;background:radial-gradient(circle at 50% 30%,#e7e6ee 0%,#a8a6b9 35%,#4a4252 70%,#2c2632 100%)}

/* who we are */
.who-title{left:646px;top:796px;font-size:36px;color:var(--white)}
.who-text{left:646px;top:880px;width:420px;font-family:"Figtree",sans-serif;font-size:15px;line-height:29px;color:var(--white)}
.who-mark{left:188px;top:800px;width:382px;height:340px;display:flex;align-items:center;justify-content:center;font-family:"Noto Sans",sans-serif;font-weight:700;font-size:52px;line-height:58px;color:var(--white);text-align:center}

/* what we do */
.section-title{left:0;width:1200px;text-align:center;font-size:36px;color:var(--ink)}
.card{position:absolute;top:1414px;width:199px;height:271px;background:var(--white);border-radius:6px;box-shadow:0 4px 14px rgba(0,0,0,.12);border-bottom:4px solid var(--teal)}
.card.alt{border-bottom-color:var(--purple)}
.card-icon{position:absolute;left:56px;top:22px;width:86px;height:86px;border-radius:50%;background:#e7f7f4;border:2px dashed var(--teal-soft);display:flex;align-items:center;justify-content:center}
.card.alt .card-icon{background:#f2ebf7;border-color:#d9c6e8}
.card-link{position:absolute;left:98px;top:140px;height:36px;border-left:1px dashed #bbb}
.card-label{position:absolute;left:0;top:190px;width:100%;text-align:center;font-family:"Noto Sans",sans-serif;font-size:17px;line-height:29px;font-weight:500}
.timeline{left:120px;top:1546px;width:959px;border-top:1px dashed #9b8cb0}

/* getting involved */
.band{left:0;top:1852px;width:1200px;height:567px;background:var(--grey-band)}
.tile{position:absolute;top:2014px;width:405px;height:293px;border-radius:6px;overflow:hidden}
.tile-label{position:absolute;left:21px;bottom:16px;width:363px;height:49px;background:var(--white);border-radius:6px;display:flex;align-items:center;justify-content:space-between;padding:0 20px 0 34px;font-family:"Noto Sans",sans-serif;font-weight:600;font-size:19px}

/* contact */
.c-icon{position:absolute;left:143px;width:70px;height:70px;border-radius:50%;background:var(--purple);display:flex;align-items:center;justify-content:center}
.c-label{position:absolute;left:245px;font-size:15px;line-height:25px;color:var(--ink)}
.c-label b{font-weight:500;display:block}
.field{position:absolute;background:var(--white);border-radius:4px;box-shadow:0 2px 10px rgba(0,0,0,.12);padding:14px 18px;font-size:14.5px;color:#555}

/* footer */
.footer-title{left:0;top:3088px;width:1200px;text-align:center;font-size:42px;color:var(--white)}
.f-brand{left:111px;top:3292px;display:flex;align-items:center;gap:14px}
.f-brand .brand-mark{border-color:var(--white);width:70px;height:70px}
.f-brand .brand-name{color:var(--white);font-size:30px;line-height:30px}
.f-col{position:absolute;top:3258px;color:var(--white)}
.f-col h4{font-family:"Noto Sans",sans-serif;font-weight:600;font-size:21px;margin-bottom:8px}
.f-col a{display:block;color:var(--white);text-decoration:none;font-size:15px;line-height:27.4px;padding-left:3px}
.social{display:flex;gap:9px;margin-top:6px}
.social span{width:32px;height:32px;border-radius:50%;background:var(--white)}
.f-rule{left:120px;top:3524px;width:950px;border-top:1px solid rgba(255,255,255,.6)}
.copy{left:0;top:3540px;width:1200px;text-align:center;color:var(--white);font-size:15.5px}
</style>
</head>
<body>

<!-- hero -->
<div class="abs hero-bg"></div>
<div class="dot" style="left:372px;top:158px;width:16px;height:16px"></div>
<div class="dot" style="left:685px;top:168px;width:14px;height:14px"></div>
<div class="dot" style="left:1136px;top:284px;width:16px;height:16px"></div>
<div class="dot" style="left:362px;top:457px;width:32px;height:32px"></div>
<div class="dot" style="left:1126px;top:457px;width:32px;height:32px"></div>
<div class="dot" style="left:97px;top:578px;width:20px;height:20px"></div>

<div class="abs brand">
  <div class="brand-mark"></div>
  <div class="brand-name">Mended<br>Kept<br>Whole</div>
</div>

<div class="abs topbar">
  <span><i><svg width="14" height="14" viewBox="0 0 24 24"><path fill="#13a898" d="M6.6 10.8a15 15 0 0 0 6.6 6.6l2.2-2.2a1 1 0 0 1 1-.25 11 11 0 0 0 3.6.6 1 1 0 0 1 1 1V20a1 1 0 0 1-1 1A17 17 0 0 1 3 4a1 1 0 0 1 1-1h3.5a1 1 0 0 1 1 1c0 1.25.2 2.45.6 3.6a1 1 0 0 1-.25 1z"/></svg></i>Phone: 833-555-0142</span>
  <span><i><svg width="14" height="12" viewBox="0 0 24 20"><path fill="#13a898" d="M2 2h20v16H2z"/><path fill="none" stroke="#fff" stroke-width="2" d="M2 3l10 8 10-8"/></svg></i>Email: info@mendedkeptwhole.org</span>
</div>

<nav class="abs nav">
  <a class="active" href="#">Home</a><a href="#">About Us</a><a href="#">Meetings &amp; Events</a><a href="#">Encounter</a><a href="#">Healing Rooms</a><a href="#">Live Stream &amp; Links</a>
</nav>

<h1 class="abs heading hero-title"><span class="g">Mended,</span><br><span class="p">Kept,</span> <span class="t">Whole</span></h1>
<p class="abs hero-text">Honoring God's presence by loving the broken, saving the lost, and healing the hurting through the demonstration of His love and power.</p>
<a class="btn" href="#" style="left:108px;top:463px;width:127px;height:44px">Get Started</a>

<svg class="abs" style="left:570px;top:366px" width="50" height="48" viewBox="0 0 50 48"><path d="M25 42C10 30 4 22 8 13c3-7 12-8 17 0 5-8 14-7 17 0 4 9-2 17-17 29z" fill="none" stroke="#13a898" stroke-width="3"/></svg>

<div class="abs hero-photo-ring"></div>
<div class="abs hero-photo" role="img" aria-label="Photo of a congregation worshipping inside a church sanctuary with a cross on the front wall"></div>

<!-- who we are -->
<svg class="abs" style="left:0;top:0" width="1200" height="1210" role="img" aria-label="Purple-toned sunset landscape with a cross">
  <defs><linearGradient id="dusk" x1="0" y1="0" x2="0" y2="1"><stop offset="0" stop-color="#8a4cb4"/><stop offset=".55" stop-color="#6c3398"/><stop offset="1" stop-color="#5a2386"/></linearGradient></defs>
  <path d="M0 785C150 760 300 560 459 535C600 520 700 680 862 667C1000 660 1100 640 1200 605L1200 1208L0 1208Z" fill="url(#dusk)"/>
</svg>
<div class="abs who-mark">Mended<br>Kept<br>Whole</div>
<h2 class="abs heading who-title">Who We Are</h2>
<div class="rule" style="left:646px;top:854px;width:76px"></div>
<p class="abs who-text">Honoring God's presence by loving the broken, saving the lost, and healing the hurting through the demonstration of His love and power.<br>Mended, Kept, Whole is here to activate, proclaim and teach the love of the Father through Jesus with the guidance of the Holy Spirit.</p>
<a class="btn" href="#" style="left:646px;top:1076px;width:127px;height:42px">Read More</a>

<!-- what we do -->
<div class="dot" style="left:165px;top:1322px;width:20px;height:20px;background:#e6f4f2"></div>
<div class="dot" style="left:244px;top:1324px;width:14px;height:14px;background:#e6f4f2"></div>
<div class="dot" style="left:1059px;top:1331px;width:20px;height:20px;background:#e6f4f2"></div>
<div class="dot" style="left:1124px;top:1402px;width:20px;height:20px;background:#e6f4f2"></div>
<div class="dot" style="left:66px;top:1486px;width:20px;height:20px;background:#e6f4f2"></div>
<div class="dot" style="left:1118px;top:1494px;width:20px;height:20px;background:#e6f4f2"></div>
<h2 class="abs heading section-title" style="top:1316px">What We Do</h2>
<div class="rule" style="left:575px;top:1370px"></div>
<div class="abs timeline"></div>
<div class="abs" style="left:112px;top:1538px;width:16px;height:16px;border:1px dashed #999;border-radius:50%;background:#fff"></div>
<div class="abs" style="left:1072px;top:1538px;width:16px;height:16px;border:1px dashed #999;border-radius:50%;background:#fff"></div>

<div class="card" style="left:146px"><div class="card-icon"><svg width="36" height="32" viewBox="0 0 36 32" fill="none" stroke="#13a898" stroke-width="1.6"><circle cx="18" cy="8" r="4"/><circle cx="8" cy="13" r="3.5"/><circle cx="28" cy="13" r="3.5"/><path d="M11 28c0-6 3-9 7-9s7 3 7 9M2 28c0-5 2-8 6-8M34 28c0-5-2-8-6-8"/></svg></div><div class="card-link"></div><div class="card-label">Worship<br>Gatherings</div></div>
<div class="card alt" style="left:379px"><div class="card-icon"><svg width="34" height="34" viewBox="0 0 34 34" fill="none" stroke="#6a2c95" stroke-width="1.6"><circle cx="17" cy="12" r="4"/><path d="M9 28c0-6 4-9 8-9s8 3 8 9M4 30h26M17 2v3M9 5l2 2M25 5l-2 2"/></svg></div><div class="card-link"></div><div class="card-label">Healing Rooms<br>Ministry</div></div>
<div class="card" style="left:613px"><div class="card-icon"><svg width="36" height="34" viewBox="0 0 36 34" fill="none" stroke="#13a898" stroke-width="1.6"><path d="M6 8h18v14H12l-6 5z"/><path d="M10 15h3l2-3 2 6 2-3h3"/><circle cx="29" cy="8" r="4"/><path d="M29 6v4M27 8h4"/></svg></div><div class="card-link"></div><div class="card-label">Pastoral Care &amp;<br>Encouragement</div></div>
<div class="card alt" style="left:847px"><div class="card-icon"><svg width="36" height="34" viewBox="0 0 36 34" fill="none" stroke="#6a2c95" stroke-width="1.6"><rect x="16" y="3" width="16" height="11" rx="1"/><path d="M19 7h10M19 10h7"/><circle cx="10" cy="16" r="3.5"/><path d="M3 31c0-6 3-9 7-9s7 3 7 9"/><circle cx="26" cy="22" r="3"/><path d="M20 31c0-4 3-6 6-6s6 2 6 6"/></svg></div><div class="card-link"></div><div class="card-label">Teaching &amp;<br>Spiritual Growth</div></div>

<a class="btn" href="#" style="left:532px;top:1721px;width:135px;height:44px">View More</a>

<!-- getting involved -->
<div class="abs band"></div>
<h2 class="abs heading section-title" style="top:1912px">Getting Involved</h2>
<div class="rule" style="left:575px;top:1966px"></div>
<div class="tile" style="left:170px"><div style="position:absolute;inset:0;background:linear-gradient(180deg,#6f7a67 0%,#a8a59c 45%,#5a4f52 100%)" role="img" aria-label="Photo of a smiling group of ministry members outdoors"></div><div class="tile-label">Giving<svg width="26" height="26" viewBox="0 0 26 26" fill="none" stroke="#13a898" stroke-width="1.8"><circle cx="13" cy="13" r="11"/><path d="M8 13h10M14 9l4 4-4 4"/></svg></div></div>
<div class="tile" style="left:624px"><div style="position:absolute;inset:0;background:linear-gradient(180deg,#8a7a5e 0%,#3e4470 45%,#2a2836 100%)" role="img" aria-label="Photo of a congregation raising hands in worship"></div><div class="tile-label">Gathering Invitation<svg width="26" height="26" viewBox="0 0 26 26" fill="none" stroke="#13a898" stroke-width="1.8"><circle cx="13" cy="13" r="11"/><path d="M8 13h10M14 9l4 4-4 4"/></svg></div></div>

<!-- contact -->
<h2 class="abs heading section-title" style="top:2494px">Contact Us</h2>
<div class="rule" style="left:575px;top:2547px"></div>

<div class="c-icon" style="top:2588px"><svg width="30" height="22" viewBox="0 0 30 22"><rect width="30" height="22" rx="2" fill="#fff"/><path d="M1 2l14 11 14-11" fill="none" stroke="#6a2c95" stroke-width="2.5"/></svg></div>
<div class="c-label" style="top:2596px"><b>EMAIL:</b>hello@mendedkeptwhole.org</div>
<div class="c-icon" style="top:2692px"><svg width="28" height="28" viewBox="0 0 24 24"><path fill="#fff" d="M6.6 10.8a15 15 0 0 0 6.6 6.6l2.2-2.2a1 1 0 0 1 1-.25 11 11 0 0 0 3.6.6 1 1 0 0 1 1 1V20a1 1 0 0 1-1 1A17 17 0 0 1 3 4a1 1 0 0 1 1-1h3.5a1 1 0 0 1 1 1c0 1.25.2 2.45.6 3.6a1 1 0 0 1-.25 1z"/></svg></div>
<div class="c-label" style="top:2701px"><b>PHONE:</b>+1 555 014 2290</div>
<div class="c-icon" style="top:2794px"><svg width="28" height="30" viewBox="0 0 28 30" fill="none" stroke="#fff" stroke-width="2"><path d="M14 22s-7-7-7-12a7 7 0 0 1 14 0c0 5-7 12-7 12z"/><circle cx="14" cy="10" r="2.5"/><ellipse cx="14" cy="25" rx="10" ry="3"/></svg></div>
<div class="c-label" style="top:2792px"><b>ADDRESS:</b>418 Willow Creek Rd. #210<br>Brookdale, CA 90210</div>

<div class="field" style="left:484px;top:2583px;width:282px;height:48px">First Name</div>
<div class="field" style="left:778px;top:2583px;width:283px;height:48px">Last Name</div>
<div class="field" style="left:484px;top:2645px;width:282px;height:49px">Phone Number</div>
<div class="field" style="left:778px;top:2645px;width:283px;height:49px">Email</div>
<div class="field" style="left:484px;top:2708px;width:577px;height:111px">Message</div>
<a class="btn" href="#" style="left:484px;top:2840px;width:132px;height:47px;font-size:18px">Submit</a>

<!-- footer -->
<svg class="abs" style="left:0;top:2980px" width="1200" height="601"><path d="M0 159Q600 -141 1200 159L1200 601L0 601Z" fill="var(--purple)"/></svg>
<h2 class="abs heading footer-title">Get In Touch With Us</h2>
<a class="btn" href="#" style="left:517px;top:3151px;width:166px;height:46px;font-size:18px;box-shadow:0 3px 8px rgba(0,0,0,.2)">Get Involved!</a>

<div class="abs f-brand"><div class="brand-mark"></div><div class="brand-name">Mended<br>Kept<br>Whole</div></div>

<div class="f-col" style="left:409px"><h4>QUICK LINKS</h4><a href="#">Home</a><a href="#">About Us</a><a href="#">Meetings &amp; Events</a><a href="#">Encounter</a><a href="#">Healing Rooms</a><a href="#">Live Stream &amp; Links</a></div>
<div class="f-col" style="left:631px"><h4>OTHER LINKS</h4><a href="#">Privacy Policy</a><a href="#">Terms and Conditions</a><a href="#">Terms of Use</a><a href="#">Support</a><a href="#">Contact Us</a></div>
<div class="f-col" style="left:862px"><h4>FOLLOW US</h4><div class="social"><span aria-label="Social profile 1"></span><span aria-label="Social profile 2"></span><span aria-label="Social profile 3"></span><span aria-label="Social profile 4"></span></div></div>

<div class="abs f-rule"></div>
<div class="abs copy">Copyrights2025@Company Name.All Rights Reserved</div>

</body>
</html>
```